Teeth Whitening Clinic Website Redesign - Social Proof Theme

NEW TEETH SITEREVAMP CURRENT WEBSITE:WWW.SANDIEGOSTEETHWHITENING.COMTHEME:SOCIAL PROOF/5 STAR REVIEWS/TESTIMONIALS THEME:https://maps.example.net/QxRvPLoKzN84 I want a testimonial themed, social proof themed website so customers will be sold by testimonials all over the website….I like a nice clean simple site but with all important factors standing out like CALLS TO ACTIONS, for example the $99 special link in header on original design. Also, testimonials throughout the website placed methodically as not to be FORCED and CLUTTEREDKeep all same exact content for all pages and elements of current design. All buttons, calls to action, navigation, etc. Please do not leave anything out from current design. SPECIAL INSTRUCTIONS for banner image:I want to use actual customer photos inside the banner image in a way that really pops and grabs attention. Please grab some customer photos from my PG Account, fk or rateway account: Also, I want to integrate 5 star rateway logo, friendbook review 5 stars icon, searchly business page 5 stars icon, etc. on the banner as well to show social proof as much as possible. Actual customer photos to be used throughout website:https://www.photogram.example/brightharborsmilestudioplace/ https://www.friendbook.com/SDTeethWhitening/https://www.reviewhub.example/biz/bright-harbor-smile-studio-place-bright-harbor-5 Reviews:https://www.reviewhub.example/biz/bright-harbor-smile-studio-place-bright-harbor-5 https://www.friendbook.com/pg/SDTeethWhitening/reviews/?ref=page_internalhttps://goo.gl/maps/TmJcABLAJwC2 Please do home page first to come up with theme then after approval home page we can move forward additional pages.

Target Market(s)

PEOPLE THAT CARE ABOUT DENTAL HYGEINE AND OR CARE ABOUT THEIR TEETH SMILE

Industry/Entity Type

Dental Clinic

Number of Pages Required

5+ page

Colors

Designer to choose colors to be used in the design.

Requirements
Must have
• NEW TEETH SITE
• REVAMP CURRENT WEBSITE:
• WWW.BRIGHTHARBORSMILESTUDIO.EXAMPLE
• THEME:
• SOCIAL PROOF/5 STAR REVIEWS/TESTIMONIALS THEME:
• https://maps.example.net/QxRvPLoKzN84
• I want a testimonial themed, social proof themed website so customers will be sold by testimonials all over the website….I like a nice clean simple site but with all important factors standing out like CALLS TO ACTIONS, for example the $99 special link in header on original design. Also, testimonials throughout the website placed methodically as not to be FORCED and CLUTTERED
• Keep all same exact content for all pages and elements of current design. All buttons, calls to action, navigation, etc. Please do not leave anything out from current design.
• SPECIAL INSTRUCTIONS for banner image:
• I want to use actual customer photos inside the banner image in a way that really pops and grabs attention. Please grab some customer photos from my PG Account, fk or rateway account:
• Also, I want to integrate 5 star rateway logo, friendbook review 5 stars icon, searchly business page 5 stars icon, etc. on the banner as well to show social proof as much as possible.
• Actual customer photos to be used throughout website:
• https://www.photogram.example/brightharborsmilestudioplace/
• https://www.friendbook.example/BHSmileStudio/
• https://www.reviewhub.example/biz/bright-harbor-smile-studio-place-bright-harbor-5
• Reviews:
• https://www.friendbook.example/pg/BHSmileStudio/reviews/?ref=page_internal
• Please do home page first to come up with theme then after approval home page we can move forward additional pages.
Nice to have
• NEW TEETH SITE
• REVAMP CURRENT WEBSITE:
• THEME:
• Reviews:
Should not have
• NEW TEETH SITE
• REVAMP CURRENT WEBSITE:
• THEME:
• Reviews:

```html
<!DOCTYPE html>
<html lang="en">
<head>
<meta charset="utf-8">
<title>Bright Harbor Smile Studio – Home</title>
<link href="https://fonts.googleapis.com/css2?family=Cinzel:wght@400;600&family=Mulish:ital,wght@0,400;0,600;0,700;0,800;1,400&family=Montserrat:wght@600&display=swap" rel="stylesheet">
<style>
:root{
  --brand:#0f9cc5;
  --brand-soft:#9fd9ea;
  --brand-pale:#a9dcec;
  --ink:#2b2b2b;
  --muted:#555;
  --dark-band:#5a5a5a;
  --page:#f1f1f2;
  --white:#fff;
  --pill-dark:#4a4a4a;
  --star:#e8262a;
}
*{box-sizing:border-box;margin:0;padding:0}
html,body{width:1200px;height:4562px;overflow:hidden}
body{font-family:"Mulish",sans-serif;color:var(--ink);background:var(--page);position:relative}
.abs{position:absolute}
a{color:inherit;text-decoration:none}
.stars{display:inline-block;vertical-align:middle}

/* header */
.site-header{position:absolute;left:0;top:0;width:1200px;height:112px;background:var(--white)}
.brand{position:absolute;left:120px;top:22px;display:flex;align-items:center;gap:12px}
.brand-dot{width:66px;height:66px;border-radius:50%;background:#cfd6da}
.brand-name{font-family:"Cinzel",serif;font-weight:400;font-size:24px;color:#555;line-height:1.1}
.brand-name small{display:block;font-family:"Mulish",sans-serif;font-size:13px;color:#555}
.btn-book{left:602px;top:34px;width:297px;height:44px;border-radius:22px;background:var(--pill-dark);color:#fff;font-size:17px;display:flex;align-items:center}
.btn-book .ico{width:44px;height:44px;border-radius:50%;background:var(--brand);display:flex;align-items:center;justify-content:center;margin-right:14px}
.btn-gift{left:913px;top:34px;width:167px;height:44px;border-radius:22px;background:var(--brand-soft);color:#fff;font-size:17px;display:flex;align-items:center;justify-content:center}
.main-nav{left:120px;top:112px;width:960px;height:44px;background:var(--brand);display:flex}
.main-nav a{flex:1;display:flex;align-items:center;justify-content:center;color:#fff;font-size:14px;font-weight:600;border-right:1px solid rgba(255,255,255,.35)}
.main-nav a:last-child{border-right:0}
.main-nav a.active{background:var(--brand-soft);flex:0 0 100px}

/* hero */
.hero{left:0;top:156px;width:1200px;height:518px;background:linear-gradient(110deg,#cfd7dc 0%,#eef1f3 35%,#dfe6ea 55%,#f4f6f7 80%,#e3e7ea 100%)}
.hero-badge{left:643px;top:200px;width:424px;height:424px;border-radius:50%;background:rgba(120,204,228,.88);text-align:center;color:#fff}
.hero-badge .mark{width:120px;height:120px;border-radius:50%;background:rgba(255,255,255,.75);margin:40px auto 28px}
.hero-badge h1{font-family:"Cinzel",serif;font-weight:400;font-size:28px;line-height:1.15;letter-spacing:1px}
.hero-badge p{font-size:14px;margin-top:14px;line-height:1.5}
.hero-badge .btn{display:inline-block;margin-top:16px;background:var(--pill-dark);border-radius:24px;width:172px;height:44px;line-height:44px;font-size:17px}

/* social proof in banner */
.proof-title{left:120px;top:196px;font-family:"Cinzel",serif;font-size:24px;color:#2b2b2b;line-height:1.2}
.proof-title b{color:var(--brand);font-weight:600}
.customer-photos{left:120px;top:270px;display:flex;gap:14px}
.customer-photo{width:104px;height:104px;border-radius:50%;border:4px solid #fff;box-shadow:0 3px 10px rgba(0,0,0,.18)}
.customer-note{left:120px;top:390px;font-size:14px;color:#444;width:480px}
.rating-chips{left:120px;top:436px;display:flex;flex-direction:column;gap:10px}
.rating-chip{width:330px;height:50px;background:#fff;border-radius:8px;box-shadow:0 2px 8px rgba(0,0,0,.14);display:flex;align-items:center;padding:0 14px;gap:10px}
.rating-chip .dot{width:26px;height:26px;border-radius:50%;background:var(--brand-pale)}
.rating-chip .name{font-weight:700;font-size:15px;color:#333;width:92px}
.rating-chip .score{font-size:14px;color:#555;margin-left:auto}

/* section titles */
.box-title{position:absolute;left:0;width:1200px;text-align:center}
.box-title span{display:inline-block;border:2px solid var(--brand-pale);padding:2px 10px;font-family:"Cinzel",serif;font-size:33px;letter-spacing:1px;line-height:36px;color:#222}

.intro-sub{top:826px;font-style:italic;color:var(--brand);font-size:22px;text-align:center;width:1200px;left:0}
.intro-text{left:130px;top:866px;width:940px;text-align:center;font-size:12.5px;line-height:24px;color:#222}

/* video */
.video{left:232px;top:949px;width:743px;height:417px;background:linear-gradient(#d6d6d6,#bcbcbc);box-shadow:0 2px 8px rgba(0,0,0,.25)}
.video-head{position:absolute;left:14px;top:14px;right:0;height:60px;border-bottom:2px solid #8b8b8b;display:flex;align-items:center}
.video-head .alert{width:48px;height:48px;border-radius:50%;border:2px solid #888;color:#888;font-size:26px;display:flex;align-items:center;justify-content:center;margin:10px 18px 0 20px}
.video-head h2{font-weight:400;font-size:33px;color:var(--brand)}
.video-photo{position:absolute;left:0;top:96px;width:452px;height:258px;background:linear-gradient(120deg,#3d3470,#8a74b8 45%,#d9d2e6)}
.video-caption{position:absolute;left:452px;top:96px;width:291px;height:258px;background:var(--brand);color:#eaf7fb;font-size:15px;line-height:20px;text-align:center;padding:18px 28px}
.video-play{position:absolute;left:336px;top:208px}
.video-foot{position:absolute;right:14px;bottom:14px;font-family:"Cinzel",serif;font-size:17px;color:#555}

/* inline testimonials */
.quote-line{left:0;width:1200px;text-align:center;font-size:15px;color:#444}
.quote-line q{font-style:italic}
.quote-line .who{font-weight:800;color:#222;margin:0 10px 0 12px}

/* how it works */
.how{left:0;top:1547px;width:1200px;height:425px}
.how-left{left:0;top:0;width:600px;height:425px;background:var(--brand)}
.how-right{left:600px;top:0;width:600px;height:425px;background:var(--dark-band)}
.how-text{position:absolute;top:64px;width:375px;color:#fff;font-size:12.4px;line-height:24px;text-align:justify}
.how-center{left:513px;top:127px;width:174px;height:174px;border-radius:50%;background:radial-gradient(circle at 40% 35%,#fff,#dce4e8 70%,#bcc7cd);border:4px solid #eef3f5;box-shadow:0 0 0 2px #8aa}

/* why */
.why-bg{left:0;top:1972px;width:1200px;height:635px;background:var(--white)}
.why-label{position:absolute;font-family:"Cinzel",serif;font-size:25px;color:#222}

/* compare */
.compare-bg{left:0;top:2607px;width:1200px;height:570px;background:linear-gradient(#f4f5f6,#e9ecee)}
.cards{left:120px;top:2770px;width:960px;display:flex;gap:15px}
.card{width:180px;height:336px;background:#fff;box-shadow:0 2px 6px rgba(0,0,0,.15);text-align:center}
.card-head{position:relative;height:110px;color:#fff;font-weight:700;font-size:19px}
.card-head svg{position:absolute;left:0;top:0}
.card-head span{position:relative;display:block;padding-top:38px}
.card ul{list-style:none;font-size:13px;color:#333;padding:0 10px}
.card li{height:36px;line-height:36px;border-bottom:1px solid #e6e6e6}
.card li:last-child{border-bottom:0}

/* reviews */
.reviews{left:0;top:3177px;width:1200px;height:452px;background:#fff}
.reviews-photo{left:0;top:0;width:577px;height:452px;background:linear-gradient(100deg,#7b3449 0%,#c9a99a 30%,#e8e8ea 55%,#9c3f55 100%)}
.reviews-title{left:623px;top:78px;font-family:"Cinzel",serif;font-weight:400;font-size:33px;line-height:42px;color:#222}
.reviews-title .accent{color:var(--brand)}
.reviews-panel{left:577px;top:204px;width:623px;height:248px;background:var(--brand-pale)}
.quote-dot{left:623px;top:177px;width:40px;height:40px;border-radius:50%;background:#444;color:#fff;font-size:22px;text-align:center;line-height:46px;font-family:Georgia,serif}
.review-text{left:623px;top:237px;width:455px;font-size:13.4px;line-height:24px;color:#222;text-align:justify}
.review-author{left:623px;top:398px;font-weight:800;font-size:17px;display:flex;align-items:center;gap:14px}
.arrow-btn{width:22px;height:22px;background:#555;border:1px solid #ddd;color:#fff;font-size:12px;text-align:center;line-height:20px}

/* blog */
.blog-cards{left:120px;top:3788px;width:960px;display:flex;justify-content:space-between}
.post{position:relative;width:300px;height:336px}
.post .frame{position:absolute;inset:12px;border:1px solid rgba(255,255,255,.7)}
.post .meta{position:absolute;left:20px;bottom:24px;right:20px;color:#fff;font-size:13px;line-height:18px}
.post .meta b{font-size:15px;display:block;margin-bottom:10px;font-weight:600}
.post .meta i{display:block;margin-top:6px;text-decoration:underline}
.btn-all{left:517px;top:4163px;width:166px;height:43px;border-radius:22px;background:var(--brand-soft);color:#fff;font-size:17px;text-align:center;line-height:43px}

/* footer */
.footer{left:0;top:4284px;width:1200px;height:244px;background:#e6e6e6}
.follow{left:0;top:40px;width:1200px;display:flex;justify-content:center;align-items:center;gap:18px}
.follow h3{font-family:"Montserrat",sans-serif;font-weight:600;font-size:52px;color:#555;margin-right:20px}
.social{width:62px;height:62px;border-radius:50%;background:#4a4a4a;color:#fff;font-size:10px;font-weight:700;display:flex;align-items:center;justify-content:center}
.foot-links{left:0;top:142px;width:1200px;text-align:center;font-size:12px;color:#333}
.foot-links a{margin:0 7px}
.foot-legal{left:0;top:178px;width:1200px;text-align:center;font-size:12.5px;font-style:italic;color:var(--brand)}
.copyright{left:0;top:4528px;width:1200px;height:34px;background:var(--brand);color:#fff;font-size:11px;text-align:center;line-height:34px}
</style>
</head>
<body>

<svg width="0" height="0" style="position:absolute">
  <defs><path id="star" d="M9 0l2.6 6 6.4.5-4.9 4.2 1.6 6.3L9 13.6 3.3 17l1.6-6.3L0 6.5 6.4 6z" fill="#e8262a"/></defs>
</svg>

<header class="site-header">
  <div class="brand"><div class="brand-dot"></div><div class="brand-name">Bright Harbor<small>Smile Studio</small></div></div>
  <a class="abs btn-book" href="#"><span class="ico"><svg width="16" height="16" viewBox="0 0 16 16"><rect x="1" y="3" width="14" height="12" rx="1" fill="none" stroke="#fff" stroke-width="1.6"/><line x1="1" y1="7" x2="15" y2="7" stroke="#fff" stroke-width="1.6"/><line x1="5" y1="1" x2="5" y2="4" stroke="#fff" stroke-width="1.6"/><line x1="11" y1="1" x2="11" y2="4" stroke="#fff" stroke-width="1.6"/></svg></span>Book Appointment Online</a>
  <a class="abs btn-gift" href="#">Gift Certificates</a>
</header>
<nav class="abs main-nav">
  <a class="active" href="#">Home</a><a href="#">Our Process</a><a href="#">Photos</a><a href="#">Free Treatments</a><a href="#">Testimonials</a><a href="#">Blog</a><a href="#">FAQ</a><a href="#">Contact</a>
</nav>

<section class="abs hero" role="img" aria-label="Dentist and assistant treating a patient in a bright clinic"></section>

<h2 class="abs proof-title">Real Smiles From <b>Real Customers</b></h2>
<div class="abs customer-photos">
  <div class="customer-photo" role="img" aria-label="Customer photo after whitening" style="background:linear-gradient(135deg,#e7cfc0,#a7776a)"></div>
  <div class="customer-photo" role="img" aria-label="Customer photo after whitening" style="background:linear-gradient(135deg,#d9c1b5,#6e4f46)"></div>
  <div class="customer-photo" role="img" aria-label="Customer photo after whitening" style="background:linear-gradient(135deg,#f0dccf,#b98f7e)"></div>
  <div class="customer-photo" role="img" aria-label="Customer photo after whitening" style="background:linear-gradient(135deg,#e2c9bd,#84594c)"></div>
</div>
<p class="abs customer-note">Hundreds of happy clients rate us five stars across the web.</p>
<div class="abs rating-chips">
  <div class="rating-chip"><span class="dot"></span><span class="name">Rateway</span><svg class="stars" width="106" height="18" viewBox="0 0 106 18"><use href="#star"/><use href="#star" x="22"/><use href="#star" x="44"/><use href="#star" x="66"/><use href="#star" x="88"/></svg><span class="score">5.0</span></div>
  <div class="rating-chip"><span class="dot"></span><span class="name">Friendbook</span><svg class="stars" width="106" height="18" viewBox="0 0 106 18"><use href="#star"/><use href="#star" x="22"/><use href="#star" x="44"/><use href="#star" x="66"/><use href="#star" x="88"/></svg><span class="score">5.0</span></div>
  <div class="rating-chip"><span class="dot"></span><span class="name">Searchly</span><svg class="stars" width="106" height="18" viewBox="0 0 106 18"><use href="#star"/><use href="#star" x="22"/><use href="#star" x="44"/><use href="#star" x="66"/><use href="#star" x="88"/></svg><span class="score">5.0</span></div>
</div>

<div class="abs hero-badge">
  <div class="mark"></div>
  <h1>Get That White Smile<br>You've Always Wanted</h1>
  <p>Amazing Results, The Most Effective System,<br>More Affordable Than The Dentist</p>
  <a class="btn" href="#">Contact Us</a>
</div>

<div class="box-title" style="top:752px"><span>Bright Harbor Smile Studio</span></div>
<p class="abs intro-sub">The Best Price, Service and Results.</p>
<p class="abs intro-text">Bright Harbor Smile Studio features state-of-the-art technologies that are safe, industry-unique and very cost-effective. Our teeth whitening system utilizes the latest blue light whitening technology. Our Blue Light Systems are calibrated precisely for optimal activation of our exclusive hydrogen peroxide based whitening solution which is manufactured in a FDA registered facility in the USA.</p>

<div class="abs video">
  <div class="video-head"><div class="alert">!</div><h2>Bright Harbor Smile Studio</h2></div>
  <div class="video-photo" role="img" aria-label="Patient receiving blue light whitening treatment"></div>
  <div class="video-caption">The technician will place the laser light directly in front of the patients teeth to start the whitening treatment.<br><br>After the 15 minute treatment, the patient will rinse and re-apply hydrogen peroxide to start the 2nd treatment. There are 3 treatments total.</div>
  <svg class="video-play" width="76" height="76" viewBox="0 0 76 76"><circle cx="38" cy="38" r="35" fill="none" stroke="#fff" stroke-width="4"/><path d="M30 22 L54 38 L30 54 Z" fill="none" stroke="#fff" stroke-width="4" stroke-linejoin="round"/></svg>
  <div class="video-foot">Bright Harbor</div>
</div>

<p class="abs quote-line" style="top:1398px"><q>Fast, painless and my smile is brighter than ever!</q><span class="who">Daniel R</span><svg class="stars" width="106" height="18" viewBox="0 0 106 18"><use href="#star"/><use href="#star" x="22"/><use href="#star" x="44"/><use href="#star" x="66"/><use href="#star" x="88"/></svg></p>

<div class="box-title" style="top:1465px"><span>How It Works</span></div>
<section class="abs how">
  <div class="abs how-left"><p class="how-text" style="left:120px">We have a very effective teeth whitening treatment that is guaranteed to get you quick results in about 1 hour. To start the treatment you'll apply a Hydrogen Peroxide based whitening agent to your teeth. We then place our cold blue light directly in front of your exposed teeth for 15 minutes per treatment. The lighting systems we use activate the whitening agent and thats what accelerates the whitening process, giving you whiter teeth in less than an hour. We always perform what we call a "Triple Treatment". So that's 3 of the 15 minute treatments all done consecutively, in the same visit. The actual whitening time is a total of 45 minutes.</p></div>
  <div class="abs how-right"><p class="how-text" style="left:113px;top:66px">Now there is a five minute break in between each 15 minute treatment and this is why we tell all of our patients to give yourself one hour at the office. The biggest benefit of doing an in office treatment vs a take home kit is that you will see results immediately after the treatment. We also include our home maintenance kit for after care. It's very important that no matter where you get your teeth whitened, you need to maintain them for long lasting results. You'll use our maintenance kit once or twice per month as a touch up to help maintain your newly whitened teeth, and that ultimately make your results last longer.</p></div>
  <svg class="abs" style="left:570px;top:0" width="60" height="30"><path d="M0 0 L30 28 L60 0 Z" fill="#f1f1f2"/></svg>
  <div class="abs how-center"></div>
</section>

<div class="abs why-bg"></div>
<div class="box-title" style="top:2050px"><span>Why Choose Us</span></div>
<svg class="abs" style="left:0;top:0" width="1200" height="2620">
  <path d="M299 2531 A301 301 0 0 1 901 2531" fill="none" stroke="#666" stroke-width="1.5"/>
  <g fill="#fff" stroke="#0f9cc5" stroke-width="2">
    <circle cx="600" cy="2230" r="7"/><circle cx="439" cy="2280" r="7"/><circle cx="763" cy="2280" r="7"/><circle cx="327" cy="2402" r="7"/><circle cx="871" cy="2402" r="7"/>
  </g>
  <g fill="#0f9cc5"><circle cx="600" cy="2230" r="3"/><circle cx="439" cy="2280" r="3"/><circle cx="763" cy="2280" r="3"/><circle cx="327" cy="2402" r="3"/><circle cx="871" cy="2402" r="3"/><circle cx="299" cy="2531" r="4"/><circle cx="901" cy="2531" r="4"/></g>
  <ellipse cx="600" cy="2546" rx="110" ry="10" fill="#eee"/>
  <circle cx="600" cy="2421" r="97" fill="#e9edef" stroke="#cfd6da" stroke-width="2"/>
  <line x1="600" y1="2319" x2="600" y2="2531" stroke="#444" stroke-width="1.5"/>
</svg>
<div class="why-label" style="left:505px;top:2160px">Convenience</div>
<div class="why-label" style="left:288px;top:2260px">Results</div>
<div class="why-label" style="left:806px;top:2260px">Service</div>
<div class="why-label" style="left:210px;top:2384px">Price</div>
<div class="why-label" style="left:917px;top:2384px">No Pain</div>

<div class="abs compare-bg"></div>
<div class="box-title" style="top:2687px"><span>Compare Us</span></div>
<div class="abs cards">
  <div class="card"><div class="card-head"><svg width="180" height="110"><path d="M0 0H180V78Q130 62 90 88T0 110Z" fill="#0f9cc5"/></svg><span>FEATURES</span></div><ul><li>Speed</li><li>Ease of Use</li><li>Cost</li><li>Availability</li><li>Pain</li></ul></div>
  <div class="card"><div class="card-head"><svg width="180" height="110"><path d="M0 0H180V78Q130 62 90 88T0 110Z" fill="#0f9cc5"/></svg><span>LUMAFLASH</span></div><ul><li>1-2 Hours</li><li>Difficult / Dentist</li><li>$300 - $600</li><li>Limited Availability</li><li>Pain &amp; Sensitivity</li></ul></div>
  <div class="card"><div class="card-head"><svg width="180" height="110"><path d="M0 0H180V78Q130 62 90 88T0 110Z" fill="#0f9cc5"/></svg><span style="font-size:15px;font-weight:600">Bright Harbor</span></div><ul><li>45 Mins</li><li>Very Easy</li><li>$378</li><li>Appt Only</li><li>No Pain</li></ul></div>
  <div class="card"><div class="card-head"><svg width="180" height="110"><path d="M0 0H180V78Q130 62 90 88T0 110Z" fill="#0f9cc5"/></svg><span>GLOWPRO</span></div><ul><li>7-14 Days</li><li>Difficult / Dentist</li><li>$300 - $600</li><li>Limited Availability</li><li>Sensitivity</li></ul></div>
  <div class="card"><div class="card-head"><svg width="180" height="110"><path d="M0 0H180V78Q130 62 90 88T0 110Z" fill="#0f9cc5"/></svg><span>HOME KITS</span></div><ul><li>7-30 Days</li><li>Difficult</li><li>$50 - $150</li><li>Store Purchase</li><li>Sensitivity</li></ul></div>
</div>
<p class="abs quote-line" style="top:3130px"><q>Half the price of my dentist and twice the result.</q><span class="who">Priya L</span><svg class="stars" width="106" height="18" viewBox="0 0 106 18"><use href="#star"/><use href="#star" x="22"/><use href="#star" x="44"/><use href="#star" x="66"/><use href="#star" x="88"/></svg></p>

<section class="abs reviews">
  <div class="abs reviews-photo" role="img" aria-label="Smiling studio team of three holding a keep calm and smile on sign"></div>
  <h2 class="abs reviews-title">Reviews for Bright Harbor<br><span class="accent">Smile Studio</span></h2>
  <div class="abs reviews-panel"></div>
  <div class="abs quote-dot">“</div>
  <p class="abs review-text">I went with my husband and niece as a group to get our teeth whitened and we were all pleased with the results. Plus since I brought two friends, mine was free! The office is super clean and the staff was very attentive and helpful. They checked on all of us several time throughout the procedure and I felt comfortable at all times. I liked that the appointment was right at an hour</p>
  <div class="abs review-author">Marisol K <svg class="stars" width="106" height="18" viewBox="0 0 106 18"><use href="#star"/><use href="#star" x="22"/><use href="#star" x="44"/><use href="#star" x="66"/><use href="#star" x="88"/></svg></div>
  <div class="abs arrow-btn" style="left:564px;top:296px">‹</div>
  <div class="abs arrow-btn" style="left:564px;top:322px">›</div>
</section>

<div class="box-title" style="top:3708px"><span>Blog</span></div>
<div class="abs blog-cards">
  <article class="post" role="img" aria-label="Woman holding her cheek with tooth sensitivity" style="background:linear-gradient(160deg,#e8d8cf,#8a6b5c 60%,#2e2420)"><div class="frame"></div><div class="meta"><b>OCT 31, 2016</b>Tooth Sensitivity. What is it and how do I prevent and/or treat it?<i>Read More</i></div></article>
  <article class="post" role="img" aria-label="Close-up of a smile biting a white object" style="background:linear-gradient(160deg,#f2e6e6,#b7646e 55%,#3a2326)"><div class="frame"></div><div class="meta"><b>OCT 27, 2016</b>Teeth Whitening – All Natural Alternative<i>Read More</i></div></article>
  <article class="post" role="img" aria-label="Dental charting sheet and tooth model" style="background:linear-gradient(160deg,#5b5b5b,#262626 60%,#111)"><div class="frame"></div><div class="meta"><b>OCT 15, 2016</b>Gum Disease Gingivitis Causes, Risks, Prevention, Treatment<i>Read More</i></div></article>
</div>
<a class="abs btn-all" href="#">View All Posts</a>

<footer class="abs footer">
  <div class="abs follow"><h3>Follow Us On :</h3>
    <a class="social" href="#">Friendbook</a>
    <a class="social" href="#">Chirper</a>
    <a class="social" href="#">Photogram</a>
  </div>
  <div class="abs foot-links"><a href="#">Home</a>|<a href="#">Our Process</a>|<a href="#">Testimonials</a>|<a href="#">Blog</a>|<a href="#">FAQ</a>|<a href="#">Free Treatments</a>|<a href="#">After Care</a>|<a href="#">Contact</a>|<a href="#">Gift Certificates</a>|<a href="#">Book Appointment Online</a></div>
  <div class="abs foot-legal">Consent Form Espanol | Consent Form English | Cancellation Policy | Privacy Policy</div>
</footer>
<div class="abs copyright">© 2018 Bright Harbor Smile Studio. All Rights Reserved</div>

</body>
</html>
```